Every Shelf Set Neatly or ESN Organized needs a business card design. ESN Organized is a professi

We need a business card design that is clean, sharp and conveys a sense of organization. I already have a logo.

Target Market(s)

Families (specifically mothers), small business owners, parents, seniors

Industry/Entity Type

Business

Contact Information for Business Card

My website is www.esnorganized-example.com and my Facebook page is http://www.sociallink-example.com/everyshelfsetneatly. The phone number is 418-552-7094 and I want to be listed as Lorna M. Pelham, Owner

Requirements
Must have
• My logo.

```html
<!DOCTYPE html>
<html lang="en">
<head>
<meta charset="utf-8">
<title>ESN Organized — Business Card</title>
<link rel="stylesheet" href="https://fonts.googleapis.com/css2?family=Montserrat:wght@400;500;700&display=swap">
<style>
  :root {
    --backdrop: #2a2a2a;
    --card-dark: #000000;
    --card-light: #f1f1f0;
    --brand-blue: #0a78d4;
    --brand-blue-deep: #075fa8;
    --text-light: #ffffff;
  }
  * { margin: 0; padding: 0; box-sizing: border-box; }
  html, body { width: 1200px; height: 840px; overflow: hidden; }
  body {
    background: var(--backdrop);
    font-family: "Montserrat", Arial, sans-serif;
    position: relative;
  }
  .card {
    position: absolute;
    left: 320px;
    width: 560px;
    height: 320px;
    overflow: hidden;
  }
  .card--front { top: 80px; background: var(--card-dark); }
  .card--back { top: 440px; background: var(--card-light); }
  .accent-area {
    position: absolute;
    inset: 0;
    clip-path: polygon(430px 0, 560px 0, 560px 320px, 240px 320px);
    background: linear-gradient(135deg, var(--brand-blue) 0%, var(--brand-blue-deep) 100%);
    opacity: 0.9;
  }
  .contact-block { position: absolute; left: 44px; top: 26px; }
  .holder-name { color: var(--brand-blue); font-weight: 700; font-size: 22px; letter-spacing: 0.3px; line-height: 1.15; }
  .holder-role { color: var(--text-light); font-weight: 400; font-size: 16px; line-height: 1.2; }
  .contact-list { list-style: none; margin-top: 18px; }
  .contact-list li {
    color: var(--text-light);
    font-size: 16px;
    line-height: 21.5px;
    display: flex;
    align-items: center;
    gap: 7px;
  }
  .contact-icon { width: 14px; height: 14px; flex: none; }
  .contact-icon * { fill: var(--brand-blue); }
  .brand-name {
    position: absolute;
    left: 32px;
    top: 30px;
    display: flex;
    align-items: center;
    gap: 10px;
    color: var(--brand-blue);
    font-weight: 500;
    font-size: 30px;
    letter-spacing: 1px;
  }
  .brand-dot { width: 14px; height: 14px; border-radius: 50%; background: var(--brand-blue); }
</style>
</head>
<body>

<section class="card card--front" aria-label="Card front">
  <div class="accent-area" role="img" aria-label="Blue diagonal stripe decoration"></div>
  <div class="contact-block">
    <p class="holder-name">Lorna M. Pelham</p>
    <p class="holder-role">Owner</p>
    <ul class="contact-list">
      <li>
        <svg class="contact-icon" viewBox="0 0 24 24" aria-hidden="true"><path d="M6.6 10.8a15.1 15.1 0 0 0 6.6 6.6l2.2-2.2a1 1 0 0 1 1-.25 11.4 11.4 0 0 0 3.6.57 1 1 0 0 1 1 1V20a1 1 0 0 1-1 1A17 17 0 0 1 3 4a1 1 0 0 1 1-1h3.5a1 1 0 0 1 1 1c0 1.25.2 2.45.57 3.57a1 1 0 0 1-.25 1z"/></svg>
        418-552-7094
      </li>
      <li>
        <svg class="contact-icon" viewBox="0 0 24 24" aria-hidden="true"><circle cx="12" cy="12" r="11"/></svg>
        www.esnorganized-example.com
      </li>
      <li>
        <svg class="contact-icon" viewBox="0 0 24 24" aria-hidden="true"><rect x="1" y="1" width="22" height="22" rx="2"/></svg>
        everyshelfsetneatly
      </li>
    </ul>
  </div>
</section>

<section class="card card--back" aria-label="Card back">
  <div class="accent-area" role="img" aria-label="Blue diagonal stripe decoration"></div>
  <div class="brand-name">
    <span class="brand-dot" aria-hidden="true"></span>
    <span>ESN Organized</span>
  </div>
</section>

</body>
</html>
```